Global Beard Oil Review Business needs a refresh

topwhiskertonic.net is a global business who's mission is to curate all available beard oils from around the world, review and grade them and present this curated collection to the user of the website.

The scope of this job includes the web site design and the design of a suitable logo to be used in the site header.

The existing site can be seen on http://topwhiskertonic.net, however this is a mock-up only the style and logo should NOT be used. This is to give you an idea of the concept of the site only.

This job is for PSD design only.

See attached design brief for detailed design requirements.
Updates

Project Deadline Extended
Reason: Extending deadline by 5 days to allow for final submissions

Target Market(s)

Men's grooming / retail

Industry/Entity Type

Retail

Number of Pages Required

2 page

Font styles to use
Sans Serif

Requirements
Must have
• 1) Comparison Table
• 2) Side Bar
• 3) Header area
• 4) Photo of Delvin Marsk (attached - can be circular or "cut-out")
• 5) Cool beard-oriented custom design background (e.g., stylistic black/brown on brown/orange beard background. I envision this beard background "drawing" rather than photo based)
• (see attached design requirements for details)
Nice to have
• Signature style writing at top with name "Delvin Marsk"
Should not have
• Do NOT use the look & feel or logo from the existing site.

```html
<!DOCTYPE html>
<html lang="en">
<head>
<meta charset="utf-8">
<title>Top Whisker Tonic</title>
<link href="https://fonts.googleapis.com/css2?family=Lato:ital,wght@0,400;0,700;1,400&family=Oranienbaum&family=Berkshire+Swash&display=swap" rel="stylesheet">
<style>
:root{
  --page-grey:#8e8e8e;
  --parchment:#e6d3a0;
  --parchment-dark:#cdb179;
  --brown:#8a5a1e;
  --brown-deep:#6e4412;
  --ink:#2a2420;
  --panel:#efedea;
  --row-a:#b68b52;
  --row-b:#a87c46;
  --table-head:#3a3a3a;
  --black:#0b0b0b;
  --white:#ffffff;
  --muted:#5a5550;
  --date:#9a6a28;
}
*{box-sizing:border-box;margin:0;padding:0}
html,body{width:708px;height:1200px;overflow:hidden}
body{position:relative;background:var(--page-grey) radial-gradient(circle at 30% 40%,#999 0,#888 70%);font-family:'Lato',sans-serif;color:var(--ink)}
.abs{position:absolute}
.column{left:78px;top:0;width:551px;height:1034px;background:linear-gradient(180deg,#ecdcae 0,#dcc48e 40%,#d8bf88 100%);border-left:2px solid #2c2416;border-right:2px solid #2c2416}
.header .brand{left:86px;top:12px;display:flex;align-items:center;gap:8px}
.brand-dot{width:30px;height:30px;border-radius:50%;background:var(--brown)}
.brand-name{font-family:'Lato',sans-serif;font-weight:700;color:var(--brown);font-size:17px;line-height:19px;letter-spacing:1px}
.contact{top:32px;display:flex;align-items:center;gap:6px}
.contact .icon{width:18px;height:18px;border-radius:50%;background:var(--brown);display:flex;align-items:center;justify-content:center}
.contact small{display:block;font-size:6px;font-style:italic;color:var(--brown-deep);font-weight:700}
.contact span{font-size:8.5px;color:var(--ink)}
.nav{left:20px;top:76px;width:668px;height:32px}
.nav ul{position:absolute;left:50px;top:0;width:568px;height:30px;display:flex;justify-content:space-around;align-items:center;list-style:none}
.nav li{font-size:7.5px;font-weight:700;color:#fff;letter-spacing:.3px}
.hero{left:86px;top:116px;width:536px;height:222px;background:#fff;padding:5px}
.hero-photo{width:100%;height:100%;background:linear-gradient(180deg,#6f7466 0,#8e9184 35%,#a99c80 55%,#9e2c2c 80%,#3a1414 100%)}
.hero-title{left:131px;top:168px;font-family:'Berkshire Swash',cursive;color:#fff;font-size:26px;line-height:28px}
.hero-copy{left:131px;top:231px;width:150px;font-size:7px;line-height:10px;color:#fff}
.btn{display:inline-block;font-size:6.5px;font-weight:700;color:#fff;text-align:center}
.btn-gold{left:132px;top:267px;width:61px;height:17px;line-height:17px;background:#a0681e}
.arrow{width:20px;height:20px;border-radius:50%;background:#a0681e;border:2px solid #fff;top:217px}
.about{left:87px;top:346px;width:535px;height:688px;background:var(--panel)}
.h2{font-family:'Oranienbaum',serif;color:var(--ink)}
.about-title{left:87px;top:356px;width:535px;text-align:center;font-size:19px}
.rule{height:1px;background:#bbb}
.about-copy{left:94px;top:397px;width:520px;text-align:center;font-size:7px;line-height:12px;color:var(--muted)}
.btn-dark{background:#1a1a1a;border:1px solid #a0681e;height:18px;line-height:16px}
.authority-title{left:90px;top:478px;font-size:19px}
.intro{left:91px;top:518px;width:380px;font-size:7px;line-height:12px;color:var(--muted)}
.compare{left:90px;top:576px;width:385px;border-collapse:collapse;table-layout:fixed;font-size:6px;color:#fff}
.compare th{background:var(--table-head);height:23px;font-weight:400;font-size:7px;text-align:left;padding:0 5px;line-height:8px;border-right:1px solid #555}
.compare td{height:63.5px;vertical-align:top;padding:8px 5px 0;border-right:1px solid rgba(255,255,255,.18);line-height:9px}
.compare tr:nth-child(odd) td{background:var(--row-a)}
.compare tr:nth-child(even) td{background:var(--row-b)}
.thumb{width:51px;height:35px;background:linear-gradient(160deg,#3d2410,#a4713c 60%,#e6dccb);border:1px solid #fff}
.pname{font-weight:700;font-size:6.5px;margin-top:1px;line-height:7px}
.score{display:flex;justify-content:space-between;line-height:12.5px}
.buy{display:block;margin:14px auto 0;width:56px;height:17px;line-height:17px;background:#1c1c1c;font-size:6.5px;font-weight:700;text-align:center}
.blog-title{left:490px;top:478px;font-size:19px}
.post{left:490px;width:126px;height:54px;display:flex;gap:4px;border-bottom:1px solid #d9d6d2}
.post .pic{width:43px;height:36px;flex:none;background:linear-gradient(120deg,#c68a5a,#e8c9a6 50%,#b6484e)}
.post p{font-size:6.3px;line-height:9.6px;color:var(--muted)}
.post em{color:var(--date);display:block}
.post b{color:#b07a33;font-weight:400}
.footer{left:0;top:1034px;width:708px;height:144px;background:var(--black);color:#fff}
.foot-h{font-family:'Oranienbaum',serif;font-size:9.5px;padding-bottom:7px;border-bottom:1px solid #333}
.links{list-style:none;font-size:7px;line-height:15.2px;margin-top:9px}
.field{background:#fff;color:#666;font-size:5.5px;padding:3px 4px;margin-bottom:5px;width:108px}
.social li{display:flex;align-items:center;gap:6px;font-size:6.5px;height:25px;border-bottom:1px solid #2a2a2a}
.social i{width:11px;height:11px;background:#3a5a96;display:block}
.foot-brand{left:490px;top:1084px;display:flex;align-items:center;gap:9px}
.foot-brand .brand-dot{width:34px;height:34px;background:#c9c9c9}
.foot-brand .brand-name{color:#e6e6e6;font-size:18px;line-height:20px}
.copy{left:0;top:1178px;width:708px;height:22px;background:#9a6a22;color:#fff;font-size:6px;text-align:center;line-height:22px}
</style>
</head>
<body>
<div class="abs column"></div>

<header class="header">
  <div class="abs brand"><span class="brand-dot"></span><span class="brand-name">TOP WHISKER<br>TONIC</span></div>
  <div class="abs contact" style="left:416px">
    <span class="icon"><svg width="9" height="9" viewBox="0 0 10 10"><path d="M2 1l2 2-1 1.2c.6 1.3 1.5 2.2 2.8 2.8L7 6l2 2-1.3 1.3C4.5 9 1 5.5.7 2.3z" fill="#fff"/></svg></span>
    <div><small>Call Us:</small><span>123-456-7890</span></div>
  </div>
  <div class="abs contact" style="left:508px">
    <span class="icon"><svg width="10" height="8" viewBox="0 0 10 8"><rect x=".5" y=".5" width="9" height="7" fill="none" stroke="#fff"/><path d="M.5.5L5 4.5 9.5.5" fill="none" stroke="#fff"/></svg></span>
    <div><small>Email Id :</small><span>hello@topwhiskertonic.net</span></div>
  </div>
</header>

<nav class="abs nav">
  <svg width="668" height="32" viewBox="0 0 668 32">
    <path d="M0 14L30 4h20v26H30L8 26l12-6z" fill="#9b6520"/>
    <path d="M668 14l-30-10h-20v26h20l22-4-12-6z" fill="#9b6520"/>
    <rect x="50" y="0" width="568" height="30" fill="#9a6420"/>
    <rect x="50" y="3" width="568" height="24" fill="none" stroke="#c89a55" stroke-dasharray="3 2" stroke-width=".7"/>
  </svg>
  <ul><li>HOME</li><li>ABOUT ME</li><li>BEARD OIL REVIEW METHODOLOGY</li><li>OUR CHARTER</li><li>BLOG</li></ul>
</nav>

<section class="abs hero">
  <div class="hero-photo" role="img" aria-label="Reviewer giving a thumbs up beside a bottle of beard oil on a red plaid blanket"></div>
</section>
<h1 class="abs hero-title">Timberline<br>Beard Oil</h1>
<p class="abs hero-copy">Lorem ipsum dolor sit amet, consectetuer adipiscing elit, sed diam nonummy nibh.</p>
<span class="abs btn btn-gold">BUY NOW</span>
<span class="abs arrow" style="left:77px"><svg width="16" height="16" viewBox="0 0 16 16"><path d="M9.5 4.5L6 8l3.5 3.5" fill="none" stroke="#fff" stroke-width="1.6"/></svg></span>
<span class="abs arrow" style="left:608px"><svg width="16" height="16" viewBox="0 0 16 16"><path d="M6.5 4.5L10 8l-3.5 3.5" fill="none" stroke="#fff" stroke-width="1.6"/></svg></span>

<main>
  <div class="abs about"></div>
  <h2 class="abs h2 about-title">About Me</h2>
  <div class="abs rule" style="left:101px;top:372px;width:200px"></div>
  <div class="abs rule" style="left:408px;top:372px;width:200px"></div>
  <svg class="abs" style="left:351px;top:379px" width="7" height="10" viewBox="0 0 7 10"><path d="M3.5 0C2 3 0 5 0 6.5a3.5 3.5 0 0 0 7 0C7 5 5 3 3.5 0z" fill="#8a5a1e"/></svg>
  <p class="abs about-copy">Lorem ipsum dolor sit amet, consectetuer adipiscing elit, sed diam nonummy nibh euismod tincidunt ut laoreet dolore magna aliquam erat volutpat. Ut wisi enim ad minim veniam, quis nostrud exerci tation ullamcorper suscipit lobortis nisl ut aliquip ex ea commodo consequat. Duis autem vel eum iriure dolor in hendrerit in vulputate velit esse molestie consequat, vel illum dolore eu feugiat nulla .</p>
  <span class="abs btn btn-dark" style="left:323px;top:440px;width:62px">READ MORE</span>

  <h2 class="abs h2 authority-title">The World’s #1 Beard Oil Authority</h2>
  <div class="abs rule" style="left:90px;top:506px;width:383px"></div>
  <p class="abs intro">Here is the master list of beard oils reviewed to date. You can link directly to the corresponding review by clicking on the name of the beard oil. In accordance with our charter, we are actively working to locate and review every single beard oil available on the planet Earth.</p>

  <table class="abs compare">
    <colgroup><col style="width:69px"><col style="width:53px"><col style="width:54px"><col style="width:52px"><col style="width:85px"><col style="width:72px"></colgroup>
    <tr><th>Product Photo<br>&amp; Name</th><th>Origin ⌄</th><th>Base Oil ⌄</th><th>Scent ⌄</th><th>Aroma, Value, Overall,<br>Therapeutic Affect,</th><th>Shop Now</th></tr>
    <tr><td><div class="thumb"></div><div class="pname">Timberline</div></td><td>Lorem<br>Ispumautem<br>vel eum<br>iriure dolor</td><td>Lorem<br>Ispumautem<br>vel eum<br>iriure dolor</td><td>Lorem<br>Ispumautem<br>vel eum<br>iriure dolor</td><td><div class="score"><span>Aroma :</span><span>7</span></div><div class="score"><span>Value :</span><span>3</span></div><div class="score"><span>Overall :</span><span>6</span></div><div class="score"><span>Therapeutic Affect :</span><span>1</span></div></td><td><span class="buy">BUY NOW</span></td></tr>
    <tr><td><div class="thumb"></div><div class="pname">Axeman</div></td><td>Lorem<br>Ispumautem<br>vel eum<br>iriure dolor</td><td>Lorem<br>Ispumautem<br>vel eum<br>iriure dolor</td><td>Lorem<br>Ispumautem<br>vel eum<br>iriure dolor</td><td><div class="score"><span>Aroma :</span><span>7</span></div><div class="score"><span>Value :</span><span>3</span></div><div class="score"><span>Overall :</span><span>6</span></div><div class="score"><span>Therapeutic Affect :</span><span>1</span></div></td><td><span class="buy">BUY NOW</span></td></tr>
    <tr><td><div class="thumb"></div><div class="pname">Brigand Beard Oil</div></td><td>Lorem<br>Ispumautem<br>vel eum<br>iriure dolor</td><td>Lorem<br>Ispumautem<br>vel eum<br>iriure dolor</td><td>Lorem<br>Ispumautem<br>vel eum<br>iriure dolor</td><td><div class="score"><span>Aroma :</span><span>7</span></div><div class="score"><span>Value :</span><span>3</span></div><div class="score"><span>Overall :</span><span>6</span></div><div class="score"><span>Therapeutic Affect :</span><span>1</span></div></td><td><span class="buy">BUY NOW</span></td></tr>
    <tr><td><div class="thumb"></div><div class="pname">Outback Beard Oil</div></td><td>Lorem<br>Ispumautem<br>vel eum<br>iriure dolor</td><td>Lorem<br>Ispumautem<br>vel eum<br>iriure dolor</td><td>Lorem<br>Ispumautem<br>vel eum<br>iriure dolor</td><td><div class="score"><span>Aroma :</span><span>7</span></div><div class="score"><span>Value :</span><span>3</span></div><div class="score"><span>Overall :</span><span>6</span></div><div class="score"><span>Therapeutic Affect :</span><span>1</span></div></td><td><span class="buy">BUY NOW</span></td></tr>
    <tr><td><div class="thumb"></div><div class="pname">Timberline</div></td><td>Lorem<br>Ispumautem<br>vel eum<br>iriure dolor</td><td>Lorem<br>Ispumautem<br>vel eum<br>iriure dolor</td><td>Lorem<br>Ispumautem<br>vel eum<br>iriure dolor</td><td><div class="score"><span>Aroma :</span><span>7</span></div><div class="score"><span>Value :</span><span>3</span></div><div class="score"><span>Overall :</span><span>6</span></div><div class="score"><span>Therapeutic Affect :</span><span>1</span></div></td><td><span class="buy">BUY NOW</span></td></tr>
    <tr><td><div class="thumb"></div><div class="pname">Axeman</div></td><td>Lorem<br>Ispumautem<br>vel eum<br>iriure dolor</td><td>Lorem<br>Ispumautem<br>vel eum<br>iriure dolor</td><td>Lorem<br>Ispumautem<br>vel eum<br>iriure dolor</td><td><div class="score"><span>Aroma :</span><span>7</span></div><div class="score"><span>Value :</span><span>3</span></div><div class="score"><span>Overall :</span><span>6</span></div><div class="score"><span>Therapeutic Affect :</span><span>1</span></div></td><td><span class="buy">BUY NOW</span></td></tr>
  </table>
  <span class="abs btn btn-dark" style="left:245px;top:1000px;width:68px;height:19px;line-height:17px">⟳ LOAD MORE</span>

  <aside>
    <h2 class="abs h2 blog-title">Blog Posts</h2>
    <div class="abs rule" style="left:490px;top:506px;width:126px;background:#8a7a66"></div>
    <div class="abs post" style="top:520px"><div class="pic" role="img" aria-label="Group of friends smiling"></div><p><em>11 Feb 2016</em>Duis autem vel eum iriure dolor in hendreri inmo vulputate velit ... <b>[+]</b></p></div>
    <div class="abs post" style="top:581px"><div class="pic" role="img" aria-label="Group of friends smiling"></div><p><em>11 Feb 2016</em>Duis autem vel eum iriure dolor in hendreri inmo vulputate velit ... <b>[+]</b></p></div>
    <div class="abs post" style="top:642px"><div class="pic" role="img" aria-label="Group of friends smiling"></div><p><em>11 Feb 2016</em>Duis autem vel eum iriure dolor in hendreri inmo vulputate velit ... <b>[+]</b></p></div>
    <div class="abs post" style="top:704px"><div class="pic" role="img" aria-label="Group of friends smiling"></div><p><em>11 Feb 2016</em>Duis autem vel eum iriure dolor in hendreri inmo vulputate velit ... <b>[+]</b></p></div>
    <div class="abs post" style="top:765px"><div class="pic" role="img" aria-label="Group of friends smiling"></div><p><em>11 Feb 2016</em>Duis autem vel eum iriure dolor in hendreri inmo vulputate velit ... <b>[+]</b></p></div>
    <div class="abs post" style="top:826px"><div class="pic" role="img" aria-label="Group of friends smiling"></div><p><em>11 Feb 2016</em>Duis autem vel eum iriure dolor in hendreri inmo vulputate velit ... <b>[+]</b></p></div>
    <div class="abs post" style="top:888px"><div class="pic" role="img" aria-label="Group of friends smiling"></div><p><em>11 Feb 2016</em>Duis autem vel eum iriure dolor in hendreri inmo vulputate velit ... <b>[+]</b></p></div>
    <div class="abs post" style="top:949px;border-bottom:none"><div class="pic" role="img" aria-label="Group of friends smiling"></div><p><em>11 Feb 2016</em>Duis autem vel eum iriure dolor in hendreri inmo vulputate velit ... <b>[+]</b></p></div>
    <span class="abs btn btn-dark" style="left:556px;top:1000px;width:60px;height:19px;line-height:17px">VIEW ALL</span>
  </aside>
</main>

<footer class="abs footer">
  <div class="abs" style="left:101px;top:12px;width:74px">
    <div class="foot-h">Quick Links</div>
    <ul class="links"><li>Home</li><li>About Us</li><li>Beard Oil Review</li><li>Methodology</li><li>Our Charter</li><li>Blogs</li></ul>
  </div>
  <div class="abs" style="left:221px;top:12px;width:108px">
    <div class="foot-h">Quick Inquiry</div>
    <div class="field" style="margin-top:8px">Name</div>
    <div class="field">Email</div>
    <div class="field" style="height:28px">Message</div>
    <span class="btn" style="background:#444;width:38px;height:14px;line-height:14px;font-size:7px">Submit</span>
  </div>
  <div class="abs" style="left:376px;top:10px;width:66px">
    <div class="foot-h">Follow Us On</div>
    <ul class="social" style="list-style:none;margin-top:2px">
      <li><i></i>Facepage</li><li><i style="background:#3ea0d8"></i>Chirper</li><li><i style="background:#c4302b"></i>Vidtube</li><li style="border:none"><i style="background:#1f6fb0"></i>Workline</li>
    </ul>
  </div>
</footer>
<div class="abs foot-brand"><span class="brand-dot"></span><span class="brand-name">TOP WHISKER<br>TONIC</span></div>
<div class="abs copy">Copyright 2016 Top Whisker Tonic. All Rights Reserved.</div>
</body>
</html>
```